Financial Services General Marketing Brochure

Need a brochure to help recipients understand what makes BWC unique and the services that we offer. Must match look/feel of website https://brightwellcustody.example Layouts should make it easy to read the content - content should not be crammed into a traditional size/layout. Please see attached creative brief for specifics.

Target Market(s)

Financial advisors and mature couples looking for trustee services.

Industry/Entity Type

Financial Service

Colors
34a7d8
ffc214

Requirements
Must have
• See Creative Brief

```html
<!DOCTYPE html>
<html lang="en">
<head>
<meta charset="utf-8">
<title>Brightwell Custody – Brochure Spread</title>
<link rel="stylesheet" href="https://fonts.googleapis.com/css2?family=Source+Serif+4:wght@400;600&family=Open+Sans:ital,wght@0,400;1,400&family=Alegreya:ital,wght@1,400;1,500&display=swap">
<style>
  :root {
    --paper: #ffffff;
    --frame: #d9d9d9;
    --fold: #c8c8c8;
    --cream: #f7f3ee;
    --heading-blue: #4d6f95;
    --body-text: #555555;
    --slate-blue: #6381a5;
    --slate-blue-deep: #4f6d93;
    --honey: #f2b347;
    --honey-line: #e9a93c;
    --white: #ffffff;
    --sun-glow: #fbf4de;
    --autumn-gold: #e3b96a;
    --autumn-amber: #c98a3e;
    --autumn-bark: #7a5432;
    --room-light: #eef0f2;
    --room-mid: #c7cfd9;
    --room-blue: #5d7fa8;
  }
  * { margin: 0; padding: 0; box-sizing: border-box; }
  html, body { width: 1200px; height: 998px; overflow: hidden; background: var(--paper); }
  body { position: relative; font-family: "Open Sans", sans-serif; color: var(--body-text); }

  .spread-frame { position: absolute; left: 1px; top: 200px; width: 1200px; height: 600px; border: 1px solid var(--frame); }
  .fold-line { position: absolute; left: 601px; top: 180px; height: 640px; border-left: 1px dashed var(--fold); }

  .info-panel { position: absolute; left: 18px; top: 217px; width: 566px; height: 318px; background: var(--cream); }
  .advisors-photo { position: absolute; left: 272px; top: 217px; width: 312px; height: 176px;
    background:
      radial-gradient(ellipse 55% 70% at 85% 80%, rgba(93,127,168,0.85) 0%, rgba(93,127,168,0) 100%),
      radial-gradient(ellipse 45% 60% at 35% 70%, rgba(120,140,170,0.55) 0%, rgba(120,140,170,0) 100%),
      linear-gradient(135deg, var(--room-light) 0%, var(--room-mid) 100%); }

  .section { position: absolute; }
  .section h2 { font-family: "Source Serif 4", serif; font-weight: 400; font-size: 17px; color: var(--heading-blue); line-height: 1; margin-bottom: 5px; }
  .section .lead { font-style: italic; font-size: 9.2px; line-height: 13px; }
  .section ul { list-style: none; font-size: 9.4px; line-height: 13px; }
  .section .bullets { margin-top: 12px; }
  .section .bullets li { padding-left: 13px; position: relative; }
  .section .bullets li::before { content: "•"; position: absolute; left: 4px; font-size: 8px; }

  .offer { left: 35px; top: 232px; }
  .serve-who { left: 35px; top: 298px; }
  .serve-how { left: 35px; top: 379px; }
  .specialties { left: 318px; top: 405px; }

  .contact-panel { position: absolute; left: 18px; top: 543px; width: 566px; height: 240px;
    background:
      radial-gradient(ellipse 35% 60% at 80% 60%, rgba(140,160,190,0.5) 0%, rgba(140,160,190,0) 100%),
      radial-gradient(ellipse 30% 60% at 20% 50%, rgba(60,85,120,0.5) 0%, rgba(60,85,120,0) 100%),
      linear-gradient(90deg, var(--slate-blue-deep) 0%, var(--slate-blue) 50%, #7590b1 100%); }
  .contact-content { position: absolute; left: 18px; top: 543px; width: 566px; height: 240px; text-align: center; color: var(--white); }
  .brand-mark { display: flex; flex-direction: column; align-items: center; }
  .brand-dot { width: 36px; height: 36px; border-radius: 50%; background: var(--honey); margin-top: 24px; }
  .brand-name { font-family: "Source Serif 4", serif; font-weight: 600; font-size: 23px; line-height: 22px; margin-top: 14px; }
  .brand-rule { width: 94px; height: 1px; background: var(--honey-line); margin: 30px auto 8px; }
  .contact-list { list-style: none; font-size: 14px; line-height: 25px; }

  .family-photo { position: absolute; left: 618px; top: 217px; width: 566px; height: 360px;
    background:
      radial-gradient(ellipse 40% 35% at 55% 30%, var(--sun-glow) 0%, rgba(251,244,222,0) 100%),
      radial-gradient(ellipse 70% 30% at 50% 95%, rgba(122,84,50,0.9) 0%, rgba(122,84,50,0) 100%),
      radial-gradient(ellipse 30% 45% at 15% 50%, rgba(150,110,70,0.55) 0%, rgba(150,110,70,0) 100%),
      radial-gradient(ellipse 30% 45% at 85% 50%, rgba(165,60,50,0.35) 0%, rgba(165,60,50,0) 100%),
      linear-gradient(180deg, #f3e6c6 0%, var(--autumn-gold) 45%, var(--autumn-amber) 75%, var(--autumn-bark) 100%); }
  .cover-badge { position: absolute; left: 776px; top: 200px; width: 250px; height: 106px; background: rgba(247, 243, 238, 0.88);
    display: flex; align-items: center; justify-content: center; gap: 14px; }
  .cover-badge .brand-dot { margin: 0; width: 46px; height: 46px; }
  .cover-badge .brand-name { margin: 0; color: var(--heading-blue); font-size: 24px; line-height: 23px; text-align: left; }

  .tagline-panel { position: absolute; left: 618px; top: 585px; width: 566px; height: 198px; background: var(--honey);
    display: flex; align-items: center; justify-content: center; }
  .tagline { font-family: "Alegreya", serif; font-style: italic; font-weight: 500; font-size: 30px; line-height: 32px; color: var(--white); text-align: center; margin-top: -4px; }
</style>
</head>
<body>
  <div class="spread-frame"></div>
  <div class="fold-line"></div>

  <div class="info-panel"></div>
  <div class="advisors-photo" role="img" aria-label="Photo of a smiling mature couple meeting with an advisor on a sofa"></div>

  <section class="section offer">
    <h2>What We Offer</h2>
    <p class="lead">We specialize exclusively in the delivery of trustee<br>and estate fiduciary services.</p>
  </section>

  <section class="section serve-who">
    <h2>Who We Serve</h2>
    <ul>
      <li>Families</li>
      <li>Professional Advisors</li>
      <li>Foundations</li>
    </ul>
  </section>

  <section class="section serve-how">
    <h2>How We Serve</h2>
    <p class="lead">Our expertise and experience is in family wealth.<br>In this regard, we serve in the following ways:</p>
    <ul class="bullets">
      <li>Trustee (Trusts)</li>
      <li>Executor and Personal Representative (Will)</li>
      <li>Agent for Financial Affairs (Power of Attorney)</li>
      <li>Trust Protector</li>
      <li>Special Independent Trustee</li>
      <li>Consultant</li>
      <li>Expert Witness</li>
    </ul>
  </section>

  <section class="section specialties">
    <h2>Trust Specialties</h2>
    <p class="lead">The general types of trusts on which we serve as trustee:</p>
    <ul class="bullets">
      <li>Family Trusts</li>
      <li>Charitable Trusts</li>
      <li>Family Foundations</li>
      <li>Life Insurance Trusts</li>
      <li>Retirement Trusts</li>
      <li>Special Needs Trusts</li>
    </ul>
  </section>

  <div class="contact-panel" role="img" aria-label="Blue-toned photo of a smiling couple at home"></div>
  <div class="contact-content">
    <div class="brand-mark">
      <span class="brand-dot"></span>
      <p class="brand-name">Brightwell<br>Custody</p>
    </div>
    <div class="brand-rule"></div>
    <ul class="contact-list">
      <li>brightwellcustody.example</li>
      <li>555-014-2876</li>
      <li>info@brightwellcustody.example</li>
    </ul>
  </div>

  <div class="family-photo" role="img" aria-label="Photo of a multi-generational family running hand in hand through sunlit autumn leaves"></div>
  <div class="cover-badge">
    <span class="brand-dot"></span>
    <p class="brand-name">Brightwell<br>Custody</p>
  </div>

  <div class="tagline-panel">
    <p class="tagline">Helping families protect and enrich<br>a multi-generational heritage</p>
  </div>
</body>
</html>
```